WordPress website design for wealth management company

A modern clean look website for a service company. This is mostly for information only, with a form to capture prospect contact information and schedule a 15 minutes call. There will be several static pages describe what services we offer, how we are different, and a blog section for posting articles and share resources. A section for client testimonials.
I want a website that is easy to understand and maintain. No proprietary plugins that cost extra. The main thing I need help is the visual layout / color palette that present a clean and professional look, select the suitable stock photos that convey the image of trust, professional, innovative, and high service.
Some websites with style I like include the following
- https://www.halvorbrook.com/
- https://www.trivanplanningworks.com/
- https://morvellfunds.com/private-equity-partners/
Also some websites in other industries with clean modern look
- https://zentrell.com/
- https://quovra.com/
- https://www.plumtorvik.com/
I want the end product to be a fully functional website that I can upload into web hosting service I use and I can easily add content and maintain myself in the future.

```html
<!DOCTYPE html>
<html lang="en">
<head>
<meta charset="utf-8">
<title>Brindlemoor Wealth</title>
<link href="https://fonts.googleapis.com/css2?family=Open+Sans:wght@400;600;700&display=swap" rel="stylesheet">
<style>
:root{
  --purple:#5b2a86;
  --purple-deep:#4a1f73;
  --purple-soft:rgba(91,42,134,.88);
  --yellow:#f6b221;
  --ink:#2b2b2b;
  --muted:#666;
  --line:#e6e6e6;
  --footer:#232323;
  --white:#fff;
}
*{margin:0;padding:0;box-sizing:border-box}
html,body{width:1200px;height:3873px;overflow:hidden}
body{font-family:"Open Sans",Arial,sans-serif;color:var(--ink);background:var(--white);position:relative}
.abs{position:absolute}

/* header */
.site-header{position:absolute;left:0;top:0;width:1200px;height:135px}
.brand{position:absolute;left:113px;top:44px;display:flex;align-items:center;gap:10px}
.brand-mark{width:34px;height:34px;border-radius:50%;background:var(--purple)}
.brand-name{font-weight:700;font-size:20px;letter-spacing:2px;color:var(--purple);line-height:1.1}
.contact-pill{position:absolute;left:725px;top:18px;display:flex;align-items:center;gap:14px}
.contact-pill .circle{width:40px;height:40px;border-radius:50%;background:var(--yellow);display:flex;align-items:center;justify-content:center}
.contact-pill p{font-size:14px;line-height:1.35;color:#333}
.contact-pill b{font-weight:600}
.btn-quote{position:absolute;left:955px;top:17px;width:134px;height:42px;background:var(--purple);color:#fff;font-size:15px;font-weight:600;display:flex;align-items:center;justify-content:center}
.header-rule{position:absolute;left:508px;top:78px;width:581px;height:1px;background:var(--line)}
.main-nav{position:absolute;top:98px;font-size:15px;color:#333}
.main-nav span{position:absolute;white-space:nowrap}

/* hero */
.hero{position:absolute;left:0;top:135px;width:1200px;height:515px;background:linear-gradient(100deg,#c89a5a 0%,#d8a866 30%,#8c6a48 55%,#e0b070 80%,#b9874e 100%)}
.hero-panel{position:absolute;left:629px;top:116px;width:571px;height:281px;background:var(--purple-soft);clip-path:polygon(40px 0,100% 0,100% 100%,0 100%)}
.hero-panel .kicker{position:absolute;left:30px;width:520px;text-align:center;top:52px;font-size:30px;line-height:1.2;color:#fff}
.hero-panel h1{position:absolute;left:30px;width:520px;top:94px;text-align:center;font-size:40px;line-height:1.2;font-weight:700;color:#fff;white-space:nowrap;letter-spacing:.5px}
.hero-panel p{position:absolute;left:72px;width:436px;top:164px;text-align:center;font-size:16px;line-height:1.75;color:#fff}

/* section titles */
.section-title{position:absolute;left:0;width:1200px;text-align:center;font-size:38px;font-weight:700;color:var(--purple);letter-spacing:.5px}

/* services */
.service-card{position:absolute;top:829px;width:236px;height:409px}
.service-card span{position:absolute;left:43px;bottom:48px;font-size:19px;font-weight:700;color:#fff;line-height:1.45}

/* different */
.different{position:absolute;left:0;top:1319px;width:1200px;height:516px;background:linear-gradient(90deg,#6f8394 0%,#8fa2b0 35%,#c7d2d8 60%,#e6ecef 100%)}
.different-panel{position:absolute;left:110px;top:119px;width:474px;height:397px;background:var(--purple);clip-path:polygon(0 0,100% 0,96% 100%,0 100%)}
.different-panel h2{position:absolute;left:36px;top:38px;font-size:40px;line-height:1.1;font-weight:700;color:#fff}
.different-panel p{position:absolute;left:36px;width:392px;font-size:15px;line-height:28px;color:#fff}
.plus-btn{position:absolute;left:536px;top:1805px;width:31px;height:30px;background:var(--yellow);color:#fff;font-size:22px;display:flex;align-items:center;justify-content:center}

/* blog */
.blog-card{position:absolute;top:2036px;width:279px;height:358px;background:#fff;box-shadow:0 2px 14px rgba(0,0,0,.08)}
.blog-card h3{position:absolute;left:33px;top:32px;font-size:19px;font-weight:400;color:#222}
.blog-card p{position:absolute;left:32px;top:70px;width:225px;font-size:15px;line-height:1.9;color:#555}
.date{font-size:15px;color:#888;display:flex;align-items:center;gap:8px}
.blog-card .date{position:absolute;left:32px;top:180px}
.blog-card .thumb{position:absolute;left:0;bottom:0;width:279px;height:138px}
.blog-item{position:absolute;left:720px;width:369px;height:128px;border-bottom:1px solid var(--line)}
.blog-item .thumb{position:absolute;left:0;top:0;width:120px;height:100px}
.blog-item p{position:absolute;left:140px;top:0;width:225px;font-size:15px;line-height:1.6;color:#444}
.blog-item .date{position:absolute;left:140px;top:58px}

/* testimonials */
.quote-photo{position:absolute;left:113px;top:2573px;width:346px;height:346px}
.quote-name{position:absolute;left:543px;top:2622px;font-size:19px;color:#222;line-height:1.45}
.quote-text{position:absolute;left:543px;top:2696px;width:550px;font-size:15px;line-height:1.9;color:#555}
.arrow{position:absolute;top:2828px;width:30px;height:30px;border-radius:50%;display:flex;align-items:center;justify-content:center}

/* schedule */
.schedule{position:absolute;left:0;top:2982px;width:1200px;height:530px;background:linear-gradient(90deg,#9fc4cf 0%,#5fb0c8 30%,#c9dfe3 60%,#eef4f5 100%)}
.schedule-panel{position:absolute;z-index:2;left:603px;top:3035px;width:487px;height:547px;background:var(--purple);clip-path:polygon(0 0,100% 0,100% 100%,4% 100%)}
.schedule-panel h2{position:absolute;left:63px;top:46px;font-size:40px;line-height:1.2;font-weight:700;color:#fff}
.field{position:absolute;left:63px;width:373px;height:49px;background:#fff;font-size:15px;color:#777;padding:14px 16px}
.btn-submit{position:absolute;left:63px;top:459px;width:151px;height:40px;background:var(--yellow);color:#fff;font-size:15px;font-weight:600;display:flex;align-items:center;justify-content:center}

/* footer */
.site-footer{position:absolute;z-index:1;left:0;top:3512px;width:1200px;height:361px;background:var(--footer);color:#fff}
.footer-brand{position:absolute;left:113px;top:60px;display:flex;align-items:center;gap:10px}
.footer-brand .brand-mark{background:#fff}
.footer-brand .brand-name{color:#fff}
.footer-nav{position:absolute;top:100px;font-size:15px;color:#fff}
.footer-nav span{position:absolute;white-space:nowrap}
.footer-rule{position:absolute;left:113px;width:976px;height:1px;background:#444}
.footer-contact{position:absolute;top:186px;display:flex;gap:14px;font-size:15px;line-height:1.7}
.footer-contact strong{font-weight:400;display:block;font-size:16px}
.social{position:absolute;z-index:2;top:3706px;width:38px;height:38px;border-radius:50%;border:1.5px solid #fff}
.copyright{position:absolute;z-index:2;left:0;top:3830px;width:1200px;text-align:center;font-size:16px;color:#ddd}
</style>
</head>
<body>

<header class="site-header">
  <div class="brand"><div class="brand-mark"></div><div class="brand-name">BRINDLEMOOR<br><span style="font-size:12px;letter-spacing:3px">WEALTH</span></div></div>
  <div class="contact-pill">
    <div class="circle"><svg width="18" height="18" viewBox="0 0 24 24" fill="#fff"><path d="M6.6 10.8a15.1 15.1 0 006.6 6.6l2.2-2.2c.3-.3.7-.4 1-.2 1.1.4 2.3.6 3.6.6.6 0 1 .4 1 1V20c0 .6-.4 1-1 1A17 17 0 013 4c0-.6.4-1 1-1h3.5c.6 0 1 .4 1 1 0 1.3.2 2.5.6 3.6.1.3 0 .7-.2 1z"/></svg></div>
    <p>Get In Touch<br><b>+1800-555-0142</b></p>
  </div>
  <div class="btn-quote">GET QUOTE</div>
  <div class="header-rule"></div>
  <nav class="main-nav">
    <span style="left:528px">Home</span><span style="left:617px">Services</span><span style="left:720px">Why Us</span><span style="left:820px">Blog</span><span style="left:895px">Testimonials</span><span style="left:1032px">Contact</span>
  </nav>
</header>

<section class="hero" role="img" aria-label="Smiling woman and older man jogging in an autumn park">
  <div class="hero-panel">
    <div class="kicker">WELCOME TO</div>
    <h1>BRINDLEMOOR WEALTH</h1>
    <p>Lorem ipsum dolor sit amet, consectetur adipiscing elit, sed do eiusmod tempor incididunt ut labore et.</p>
  </div>
</section>

<h2 class="section-title" style="top:720px">OUR SERVICES</h2>
<div class="service-card" style="left:111px;background:linear-gradient(160deg,#e7e2dc,#9d8b7c)" role="img" aria-label="Smiling woman with curly hair in a white coat"><span>FACILITY<br>STAFFING</span></div>
<div class="service-card" style="left:358px;background:linear-gradient(160deg,#eef2f6,#8ea6c0)" role="img" aria-label="MRI scanner in a bright hospital room"><span>RADIOLOGY<br>SUPPORT</span></div>
<div class="service-card" style="left:605px;background:linear-gradient(160deg,#9c7b62,#4b3a30)" role="img" aria-label="Smiling man with glasses shaking hands"><span>TRANSCRIPTION</span></div>
<div class="service-card" style="left:852px;background:linear-gradient(160deg,#5f7080,#1f2a35)" role="img" aria-label="Businesswoman holding a tablet in an office corridor"><span>BILLING AND<br>COLLECTIONS</span></div>

<section class="different" role="img" aria-label="Senior doctor and businesswoman reviewing a tablet together">
  <div class="different-panel">
    <h2>HOW WE ARE<br>DIFFERENT</h2>
    <p style="top:170px">Lorem ipsum dolor sit amet, consectetur adipiscing elit, sed do eiusmod tempor incididunt ut labore et dolore magna aliqua. Quis ipsum suspendisse ultrices gravida. Risus commodo viverra maecenas accumsan lacus vel facilisis.</p>
    <p style="top:320px">Consectetur adipiscing elit, sed do eiusmod tempor incididunt ut labore et dolore magna aliqua.</p>
  </div>
</section>
<div class="plus-btn">+</div>

<h2 class="section-title" style="top:1915px">LATEST BLOG</h2>
<article class="blog-card" style="left:113px">
  <h3>Lorem Ipsum</h3>
  <p>Lorem ipsum dolor sit amnsec tetur adipiscing elit, sed doolor sit amnsec tetur .</p>
  <div class="date"><svg width="14" height="14" viewBox="0 0 14 14" fill="none" stroke="#999"><rect x="1" y="2.5" width="12" height="10.5"/><path d="M1 5.5h12M4 1v3M10 1v3"/></svg>28/03/23</div>
  <div class="thumb" style="background:linear-gradient(90deg,#eef0ee,#d9b94a 45%,#eceae4)" role="img" aria-label="Woman in yellow shirt smiling at a desk"></div>
</article>
<article class="blog-card" style="left:408px">
  <h3>Lorem Ipsum</h3>
  <p>Lorem ipsum dolor sit amnsec tetur adipiscing elit, sed doolor sit amnsec tetur .</p>
  <div class="date"><svg width="14" height="14" viewBox="0 0 14 14" fill="none" stroke="#999"><rect x="1" y="2.5" width="12" height="10.5"/><path d="M1 5.5h12M4 1v3M10 1v3"/></svg>28/03/23</div>
  <div class="thumb" style="background:linear-gradient(120deg,#f2f4f7,#c9d2de)" role="img" aria-label="Doctor writing on a clipboard beside a laptop"></div>
</article>

<div class="blog-item" style="top:2036px">
  <div class="thumb" style="background:linear-gradient(135deg,#cfd6dc,#3b4752)" role="img" aria-label="Hand touching digital medical icons"></div>
  <p>Lorem ipsum dolor sit ametr aidunt ut labore et dolore</p>
  <div class="date"><svg width="14" height="14" viewBox="0 0 14 14" fill="none" stroke="#999"><rect x="1" y="2.5" width="12" height="10.5"/><path d="M1 5.5h12M4 1v3M10 1v3"/></svg>28/03/23</div>
</div>
<div class="blog-item" style="top:2166px">
  <div class="thumb" style="background:linear-gradient(135deg,#dfe3e6,#7a8793)" role="img" aria-label="Doctor talking with a patient in a clinic"></div>
  <p>Lorem ipsum dolor sit ametr aidunt ut labore et dolore</p>
  <div class="date"><svg width="14" height="14" viewBox="0 0 14 14" fill="none" stroke="#999"><rect x="1" y="2.5" width="12" height="10.5"/><path d="M1 5.5h12M4 1v3M10 1v3"/></svg>28/03/23</div>
</div>
<div class="blog-item" style="top:2294px">
  <div class="thumb" style="background:linear-gradient(135deg,#1d2a3a,#3f6f9a)" role="img" aria-label="Tablet showing medical scan imagery"></div>
  <p>Lorem ipsum dolor sit ametr aidunt ut labore et dolore</p>
  <div class="date"><svg width="14" height="14" viewBox="0 0 14 14" fill="none" stroke="#999"><rect x="1" y="2.5" width="12" height="10.5"/><path d="M1 5.5h12M4 1v3M10 1v3"/></svg>28/03/23</div>
</div>

<h2 class="section-title" style="top:2517px">TESTIMONIALS</h2>
<svg class="quote-photo" viewBox="0 0 346 346" aria-hidden="true">
  <path d="M310 60 L366 60 L325 120 L295 110 Z" fill="var(--yellow)" transform="translate(-24 0)"/>
  <circle cx="173" cy="173" r="165" fill="none" stroke="var(--purple)" stroke-width="18" stroke-dasharray="900 140" transform="rotate(-20 173 173)"/>
</svg>
<div class="abs" style="left:131px;top:2591px;width:310px;height:310px;border-radius:50%;background:radial-gradient(circle at 55% 45%,#d9c2ad,#8d8a86)" role="img" aria-label="Portrait of a smiling woman with long wavy hair"></div>
<div class="quote-name">Jane J,<br>Lorem Ipsum</div>
<p class="quote-text">Sed ut perspiciatis unde omnis iste natus error sit voluptatem accusantium doloremque laudantium, totam rem aperiam, eaque ipsa quae ab illo inventore veritatis et quasi architecto beatae vitae dicta sunt explicabo.</p>
<div class="arrow" style="left:543px;background:#eee"><svg width="12" height="10" viewBox="0 0 12 10" fill="none" stroke="#888" stroke-width="1.5"><path d="M11 5H1M5 1L1 5l4 4"/></svg></div>
<div class="arrow" style="left:590px;background:var(--yellow)"><svg width="12" height="10" viewBox="0 0 12 10" fill="none" stroke="#fff" stroke-width="1.5"><path d="M1 5h10M7 1l4 4-4 4"/></svg></div>

<section class="schedule" role="img" aria-label="Smiling nurses in blue scrubs with arms crossed"></section>
<form class="schedule-panel">
  <h2>SCHEDULE A 15<br>MINUTES CALL</h2>
  <div class="field" style="top:156px">Full Name</div>
  <div class="field" style="top:213px">Email Address</div>
  <div class="field" style="top:269px">Phone Number</div>
  <div class="field" style="top:326px;height:98px">Message</div>
  <div class="btn-submit">SUBMIT NOW</div>
</form>

<footer class="site-footer">
  <div class="footer-brand"><div class="brand-mark"></div><div class="brand-name">BRINDLEMOOR<br><span style="font-size:12px;letter-spacing:3px">WEALTH</span></div></div>
  <nav class="footer-nav">
    <span style="left:524px">Home</span><span style="left:612px">Services</span><span style="left:716px">Why Us</span><span style="left:815px">Blog</span><span style="left:891px">Testimonials</span><span style="left:1028px">Contact</span>
  </nav>
  <div class="footer-rule" style="top:147px"></div>
  <div class="footer-contact" style="left:113px">
    <svg width="18" height="24" viewBox="0 0 18 24" fill="none" stroke="#fff" stroke-width="1.5"><path d="M9 23s8-8 8-14A8 8 0 001 9c0 6 8 14 8 14z"/><circle cx="9" cy="9" r="3"/></svg>
    <div><strong>ADDRESS</strong>Brindlemoor Wealth,<br>Address comes here</div>
  </div>
  <div class="footer-contact" style="left:370px">
    <svg width="24" height="18" viewBox="0 0 24 18" fill="none" stroke="#fff" stroke-width="1.5"><rect x="1" y="1" width="22" height="16"/><path d="M1 1l11 9 11-9"/></svg>
    <div><strong>EMAIL</strong>info@brindlemoorwealth.com</div>
  </div>
  <div class="footer-contact" style="left:688px">
    <svg width="22" height="22" viewBox="0 0 24 24" fill="none" stroke="#fff" stroke-width="1.5"><path d="M6.6 10.8a15.1 15.1 0 006.6 6.6l2.2-2.2c.3-.3.7-.4 1-.2 1.1.4 2.3.6 3.6.6.6 0 1 .4 1 1V20c0 .6-.4 1-1 1A17 17 0 013 4c0-.6.4-1 1-1h3.5c.6 0 1 .4 1 1 0 1.3.2 2.5.6 3.6.1.3 0 .7-.2 1z"/></svg>
    <div><strong>PHONE</strong>+1800-555-0142</div>
  </div>
  <div class="footer-rule" style="top:288px"></div>
</footer>
<div class="social" style="left:958px"></div>
<div class="social" style="left:1004px"></div>
<div class="social" style="left:1049px"></div>
<p class="copyright">2023 Brindlemoor Wealth. All Rights Reserved.</p>

</body>
</html>
```